Kor'v Meridell Travel

We need a sleek, professional, inviting card to elicit global travel for the experienced and professional traveler. Royal blue, black and silver. (perhaps the wording could be silver with black shadow?-get creative) Maybe a watermark on the front and the full raised logo on the back.
We want a stylish and modern card, but professional.

```html
<!DOCTYPE html>
<html lang="en">
<head>
<meta charset="utf-8">
<title>Kor'v Meridell Travel — Business Card</title>
<link rel="stylesheet" href="https://fonts.googleapis.com/css2?family=Open+Sans:wght@400;600;700&display=swap">
<style>
  :root {
    --stage: #1a1a1b;
    --card: #1d1d1f;
    --royal-blue: #1f9fdb;
    --green: #7ac143;
    --silver: #b9bcc0;
    --text-light: #e6e6e6;
    --text-muted: #a3a3a3;
  }
  * { margin: 0; padding: 0; box-sizing: border-box; }
  html, body { width: 1200px; height: 900px; overflow: hidden; background: var(--stage); }
  body {
    font-family: "Open Sans", Arial, sans-serif;
    display: flex; flex-direction: column; align-items: center; justify-content: center; gap: 40px;
  }
  .card {
    position: relative; width: 680px; height: 388px;
    background: var(--card); overflow: hidden;
    box-shadow: 0 18px 40px rgba(0,0,0,.55);
  }
  .card::after {
    content: ""; position: absolute; left: 0; right: 0; bottom: 0; height: 8px;
    background: var(--royal-blue);
  }
  /* front */
  .brand-front {
    position: absolute; right: 48px; top: 84px;
    display: flex; align-items: center; gap: 10px;
  }
  .brand-front .brand-name {
    color: var(--royal-blue); font-weight: 700; font-size: 22px; letter-spacing: 1px;
    text-transform: uppercase; white-space: nowrap;
  }
  .brand-front .brand-dot { width: 14px; height: 14px; border-radius: 50%; background: var(--green); flex: none; }
  .holder { position: absolute; left: 48px; top: 168px; }
  .holder-name {
    color: var(--royal-blue); font-weight: 700; font-size: 24px; letter-spacing: .5px;
    text-transform: uppercase; white-space: nowrap;
  }
  .holder-title { color: var(--text-muted); font-size: 16px; margin-top: 2px; }
  .divider {
    position: absolute; left: 48px; right: 48px; top: 246px; height: 1px;
    background: var(--royal-blue);
  }
  .contact { position: absolute; left: 48px; top: 264px; list-style: none; }
  .contact li {
    display: flex; align-items: center; gap: 10px;
    color: var(--text-light); font-size: 15px; line-height: 26px;
  }
  .contact svg { width: 14px; height: 14px; fill: var(--green); flex: none; }
  .address {
    position: absolute; right: 48px; bottom: 34px; text-align: right;
    color: var(--text-light); font-size: 16px; line-height: 24px;
  }
  /* back */
  .card-back { display: flex; align-items: center; justify-content: center; }
  .brand-back { display: flex; align-items: center; gap: 14px; }
  .brand-back .brand-name {
    color: var(--silver); font-weight: 700; font-size: 36px; letter-spacing: 2px;
    text-transform: uppercase; white-space: nowrap;
  }
  .brand-back .brand-dot { width: 18px; height: 18px; border-radius: 50%; background: var(--silver); flex: none; }
</style>
</head>
<body>
  <section class="card card-front">
    <div class="brand-front">
      <span class="brand-dot"></span>
      <span class="brand-name">Kor'v Meridell Travel</span>
    </div>
    <div class="holder">
      <p class="holder-name">Daren Holloway</p>
      <p class="holder-title">President</p>
    </div>
    <div class="divider"></div>
    <ul class="contact">
      <li><svg viewBox="0 0 24 24" aria-hidden="true"><path d="M6.6 10.8a15.1 15.1 0 0 0 6.6 6.6l2.2-2.2a1 1 0 0 1 1-.25 11.4 11.4 0 0 0 3.6.57 1 1 0 0 1 1 1V20a1 1 0 0 1-1 1A17 17 0 0 1 3 4a1 1 0 0 1 1-1h3.5a1 1 0 0 1 1 1c0 1.25.2 2.450.57 3.57a1 1 0 0 1-.25 1z"/></svg>555-318-4720</li>
      <li><svg viewBox="0 0 24 24" aria-hidden="true"><path d="M2 5h20v14H2zm2 2v.4l8 5 8-5V7l-8 5z"/></svg>info@korvmeridell.com</li>
      <li><svg viewBox="0 0 24 24" aria-hidden="true"><path d="M12 2a10 10 0 1 0 0 20 10 10 0 0 0 0-20zm0 2a14 14 0 0 1 1.9 4h-3.8A14 14 0 0 1 12 4zM4.3 14a8 8 0 0 1 0-4h3.4a16.5 16.5 0 0 0 0 4zM12 20a14 14 0 0 1-1.9-4h3.8A14 14 0 0 1 12 20zm2.3-6H9.7a14.7 14.7 0 0 1 0-4h4.6a14.7 14.7 0 0 1 0 4zm2 0a16.5 16.5 0 0 0 0-4h3.4a8 8 0 0 1 0 4z"/></svg>www.korvmeridell.com</li>
    </ul>
    <p class="address">1870 Lantern Bay Walk<br>Harbor Vista CA 90001</p>
  </section>

  <section class="card card-back">
    <div class="brand-back">
      <span class="brand-dot"></span>
      <span class="brand-name">Kor'v Meridell Travel</span>
    </div>
  </section>
</body>
</html>
```